Copperleaf Roofing Business Card

This is my current business card. But I’d like to make some changes. Somewhere on the card I’d like to list some of the services we offer. Maybe on the back? But I’d still like to keep the red. White and black modern look.

-residential & commercial roofing
-Roof Repairs & Maintenance
-Storm Damage & Insurance Claims specialist
-Christmas Lights and permanent Christmas lights
Fencing. Windows. Gutters. Siding. Sheetrock, painting.

```html
<!DOCTYPE html>
<html lang="en">
<head>
<meta charset="utf-8">
<title>Copperleaf Roofing Business Card</title>
<link href="https://fonts.googleapis.com/css2?family=Michroma&family=Work+Sans:wght@400;500&display=swap" rel="stylesheet">
<style>
  :root{
    --red:#d3202a;
    --deep-red:#7a0f14;
    --dark-red:#5a0a0e;
    --black:#141414;
    --white:#ffffff;
    --card-white:#f4f4f2;
    --backdrop:#e6e6e6;
  }
  *{margin:0;padding:0;box-sizing:border-box}
  html,body{width:1200px;height:955px;overflow:hidden}
  body{background:var(--backdrop);position:relative;font-family:"Work Sans",sans-serif;color:var(--black)}
  .card{position:absolute;left:334px;width:551px;height:315px;overflow:hidden;box-shadow:0 4px 10px rgba(0,0,0,.18)}
  .card--front{top:141px}
  .card--back{top:513px;background:var(--card-white)}

  .plaid-fill{position:absolute;inset:0;background:linear-gradient(135deg,var(--red) 0%,var(--deep-red) 55%,var(--dark-red) 100%)}
  .front-mark{position:absolute;left:208px;top:45px;width:136px;height:136px;border-radius:50%;background:var(--red);border:3px solid var(--white)}
  .front-name{position:absolute;left:0;right:0;top:200px;text-align:center;font-family:"Michroma",sans-serif;font-size:25px;line-height:36px;color:var(--white);letter-spacing:1px}

  .back-mark{position:absolute;left:242px;top:19px;width:66px;height:66px;border-radius:50%;background:var(--red)}
  .back-name{position:absolute;left:0;right:0;top:94px;text-align:center;font-family:"Michroma",sans-serif;font-size:13px;line-height:17px;color:var(--red);letter-spacing:.5px}

  .person{position:absolute;right:301px;top:171px;text-align:right}
  .person__name{font-family:"Michroma",sans-serif;font-size:15px;letter-spacing:2px;color:var(--black)}
  .person__name span{color:var(--red)}
  .person__role{font-size:11.5px;color:var(--red);letter-spacing:1.5px;margin-top:1px}
  .divider{position:absolute;left:258px;width:1.5px;background:var(--red)}
  .divider--contact{top:160px;height:52px}
  .divider--services{top:250px;height:24px}

  .contacts{position:absolute;left:275px;top:152px;list-style:none}
  .contacts li{display:flex;align-items:center;height:21px;font-size:13px;letter-spacing:.6px}
  .contacts svg{width:11px;height:11px;margin-right:12px;flex:none}

  .services{position:absolute;left:0;right:0;top:247px;font-size:8.4px;font-weight:500;letter-spacing:.2px;text-transform:uppercase}
  .services__col{position:absolute;line-height:16.5px}
  .services__col--left{right:301px;text-align:right}
  .services__col--right{left:275px}
  .services__extra{position:absolute;left:0;right:0;top:33px;text-align:center}
  .strip{position:absolute;left:0;right:0;bottom:0;height:8px;background:linear-gradient(90deg,var(--deep-red),var(--red),var(--deep-red))}
</style>
</head>
<body>
  <section class="card card--front">
    <div class="plaid-fill" role="img" aria-label="Red, black and white tartan plaid pattern"></div>
    <div class="front-mark"></div>
    <p class="front-name">COPPERLEAF<br>ROOFING CO.</p>
  </section>

  <section class="card card--back">
    <div class="back-mark"></div>
    <p class="back-name">COPPERLEAF<br>ROOFING CO.</p>

    <div class="person">
      <p class="person__name">DEAN <span>CARVER</span></p>
      <p class="person__role">Owner</p>
    </div>
    <div class="divider divider--contact"></div>
    <ul class="contacts">
      <li><svg viewBox="0 0 24 24"><path fill="#d3202a" d="M6.6 10.8a15 15 0 0 0 6.6 6.6l2.2-2.2c.3-.3.7-.4 1-.2 1.1.4 2.3.6 3.6.6.6 0 1 .4 1 1V20c0 .6-.4 1-1 1A17 17 0 0 1 3 4c0-.6.4-1 1-1h3.5c.6 0 1 .4 1 1 0 1.3.2 2.5.6 3.6.1.3 0 .7-.2 1z"/></svg>555-014-2290</li>
      <li><svg viewBox="0 0 24 24"><rect x="2" y="5" width="20" height="14" fill="#d3202a"/><path d="M2 5l10 8 10-8" fill="none" stroke="#fff" stroke-width="2"/></svg>dean@copperleafroofing.co</li>
      <li><svg viewBox="0 0 24 24" fill="none" stroke="#d3202a" stroke-width="2"><circle cx="12" cy="12" r="10"/><path d="M2 12h20M12 2c3 3 3 17 0 20M12 2c-3 3-3 17 0 20"/></svg>www.copperleafroofing.co</li>
    </ul>

    <div class="services">
      <div class="services__col services__col--left">Residential &amp; Commercial Roofing<br>Storm Damage &amp; Insurance Claims Specialist</div>
      <div class="services__col services__col--right">Roof Repairs &amp; Maintenance<br>Christmas Lights and Permanent Christmas Light</div>
      <p class="services__extra">Fencing. Windows. Gutters. Siding. Sheetrock, Painting</p>
    </div>
    <div class="divider divider--services"></div>
    <div class="strip" role="img" aria-label="Thin band of red tartan plaid pattern"></div>
  </section>
</body>
</html>
```